Gearhead Rally 5, The fifth annual Gearhead Rally motorcycle event, www.gearheadrally.example

We need an event poster that can be used in print and on the web to promote our event. Files for the poster should be modifiable to add additional information as it becomes available. The Gearhead Rally is a gathering for Vintage, Classic and Cafe' Racer motorcycles and their riders, Rockers and Mods. The event date is Saturday, July 26, 2014, rain or shine, from 9:00 AM to 6:00 PM EDT at Maplewick Park, 217 North Birch Avenue, Pittston, PA 18651 USA. Friday July 25 Meet and Greet from 7:00 PM to close at Hadley's Hideaway, Pittston, PA. Early Birds' Brunch, Sunday, July 27, 7:00 to 10:00 AM, location tba. Optional Group Ride Saturday from 10:00 AM to Noon. Tarvex 450 Custom Cafe' Motorcycle Raffle, Contests, Trophies and Cash Prizes for Pin-up Girl, Coolest Cafe' Racer Motorcycle, Coolest Mod Scooter, Peoples Choice Motorcycle, and More! Live music by the one and only legendary KLTV, "Slim Jim" Varga and more tba. Brought to you by Wyland Throttlers, www.social.example/wylandthrottlers?ref=hl, Bixby and Moss/Moss Rascals, www.bixbyandmoss.example. Partial Proceeds to benefit the UFWL and The Valley Rescue Volunteers Society. More information and advance tickets available at www.gearheadrally.example
Uploaded files include: Wyland Throttlers Logo, Moss Rascal's Logo, stock vintage image, two images from 2014 event, and a photo of the bike to be raffled (better image in the works.

Thank you to all who participated in our competition.  We received excellent work from you all, and the hard part for us is having to choose.  Our decision will be made today.

```html
<!DOCTYPE html>
<html lang="en">
<head>
<meta charset="utf-8">
<title>Gearhead Rally 5 – Event Poster</title>
<link rel="stylesheet" href="https://fonts.googleapis.com/css2?family=Montserrat:wght@500;600;700&family=Roboto+Condensed:wght@400;700&display=swap">
<style>
  :root {
    --backdrop-top: #9a9a9a;
    --backdrop-bottom: #3e3e3e;
    --poster-black: #000000;
    --poster-white: #ffffff;
    --headline-grey: #6f6f6f;
    --tag-grey: #7a7a7a;
    --muted-grey: #585858;
    --rule-grey: #8a8a8a;
    --footer-ink: #111111;
  }
  * { box-sizing: border-box; margin: 0; padding: 0; }
  html, body { width: 1200px; height: 1000px; overflow: hidden; }
  body {
    background: linear-gradient(to bottom, var(--backdrop-top), var(--backdrop-bottom));
    font-family: "Montserrat", sans-serif;
    position: relative;
  }
  .poster {
    position: absolute; left: 267px; top: 0;
    width: 666px; height: 1000px;
    background: var(--poster-black);
    color: var(--poster-white);
    overflow: hidden;
  }
  .masthead { position: absolute; left: 0; top: 0; width: 666px; height: 400px; z-index: 1; }
  .masthead text { font-family: "Montserrat", sans-serif; }
  .masthead .kicker { fill: var(--headline-grey); font-weight: 600; }
  .masthead .title { fill: var(--poster-white); font-weight: 500; }
  .masthead .tagline-band { fill: var(--poster-black); }
  .masthead .tagline { fill: var(--poster-white); font-family: "Roboto Condensed", sans-serif; font-weight: 700; }

  .hero-photo {
    position: absolute; left: 22px; top: 338px; width: 620px; height: 190px; z-index: 2;
    background: radial-gradient(ellipse 48% 50% at 45% 55%, rgba(140,140,140,0.9) 0%, rgba(80,80,80,0.75) 45%, rgba(0,0,0,0) 100%);
  }
  .event-date {
    position: absolute; right: 15px; top: 398px; z-index: 3;
    font-size: 41px; font-weight: 600; letter-spacing: -0.5px;
  }
  .venue-line {
    position: absolute; left: 0; top: 535px; width: 666px; text-align: center;
    font-family: "Roboto Condensed", sans-serif; font-weight: 700;
    font-size: 10px; letter-spacing: 1.3px; text-transform: uppercase;
  }

  .side-event {
    position: absolute; width: 200px; text-align: center;
    transform: rotate(-8deg); transform-origin: center top;
  }
  .side-event--meet { left: 17px; top: 570px; }
  .side-event--brunch { left: 233px; top: 575px; }
  .side-event--ride { left: 450px; top: 570px; }
  .side-event__tag {
    background: var(--tag-grey);
    height: 64px; display: flex; align-items: center; justify-content: center;
    font-size: 22px; font-weight: 600; line-height: 1; text-transform: uppercase;
    letter-spacing: -0.3px;
  }
  .side-event__when {
    margin-top: 10px; color: var(--muted-grey);
    font-family: "Roboto Condensed", sans-serif; font-weight: 700;
    font-size: 17px; line-height: 1.2; letter-spacing: 1.2px;
  }

  .raffle {
    position: absolute; left: 0; top: 744px; width: 666px; text-align: center;
    font-size: 25px; font-weight: 600; letter-spacing: -0.3px; text-transform: uppercase;
  }
  .prizes {
    position: absolute; left: 0; top: 781px; width: 666px; text-align: center;
    color: var(--muted-grey); font-family: "Roboto Condensed", sans-serif; font-weight: 700;
    font-size: 11.5px; line-height: 1.3; letter-spacing: 1.4px; text-transform: uppercase;
  }
  .lineup {
    position: absolute; left: 17px; top: 830px; width: 633px; height: 66px;
    border: 1.5px solid var(--rule-grey);
    display: flex; align-items: center; justify-content: center; text-align: center;
    font-size: 16px; font-weight: 600; line-height: 1.25; text-transform: uppercase;
  }

  .credits {
    position: absolute; left: 0; top: 905px; width: 666px; height: 95px;
    background: var(--poster-white); color: var(--footer-ink);
  }
  .credits__label {
    position: absolute; left: 15px; top: 12px;
    font-family: "Roboto Condensed", sans-serif; font-weight: 700; font-size: 9px; letter-spacing: 0.6px;
  }
  .sponsor { position: absolute; display: flex; align-items: center; gap: 8px; }
  .sponsor--throttlers { left: 14px; top: 34px; }
  .sponsor--rascals { left: 192px; top: 34px; }
  .sponsor__mark { width: 46px; height: 46px; border-radius: 50%; background: var(--footer-ink); flex: none; }
  .sponsor__name { font-size: 11px; font-weight: 600; line-height: 1.15; }
  .sponsor__url { font-size: 5.5px; font-weight: 500; margin-top: 2px; }
  .credits__beneficiaries {
    position: absolute; left: 395px; top: 16px; width: 262px; text-align: center;
    font-size: 9.5px; font-weight: 600; line-height: 1.3;
  }
</style>
</head>
<body>
  <main class="poster">
    <svg class="masthead" viewBox="0 0 666 400" aria-labelledby="masthead-title">
      <title id="masthead-title">The Fifth Annual Gearhead Rally</title>
      <text class="kicker" x="28" y="63" font-size="66" textLength="626" lengthAdjust="spacingAndGlyphs">THE FIFTH ANNUAL</text>
      <text class="title" x="26" y="183" font-size="128" textLength="632" lengthAdjust="spacingAndGlyphs">GEARHEAD</text>
      <text class="title" x="24" y="394" font-size="285" textLength="630" lengthAdjust="spacingAndGlyphs">RALLY</text>
      <g transform="rotate(-9.4 14 323)">
        <rect class="tagline-band" x="-40" y="303" width="760" height="27"/>
        <text class="tagline" x="14" y="323" font-size="17" letter-spacing="2" textLength="636" lengthAdjust="spacingAndGlyphs">VINTAGE, CLASSIC AND CAFÉ RACER MOTORCYCLES AND THEIR RIDERS</text>
      </g>
    </svg>

    <div class="hero-photo" role="img" aria-label="Black and white halftone photo of a café racer motorcycle in side view"></div>

    <p class="event-date">JULY 26 2014</p>
    <p class="venue-line">Rain or shine. 09:00 AM to 06:00 PM EDT at Maplewick Park, 217 North Birch Avenue, Pittston, PA 18651 USA</p>

    <section class="side-event side-event--meet">
      <h2 class="side-event__tag">Meet and<br>Greet</h2>
      <p class="side-event__when">Friday, July 25<br>07:00 PM To Close<br>Hadley’s Hideaway</p>
    </section>
    <section class="side-event side-event--brunch">
      <h2 class="side-event__tag">Early Birds’<br>Brunch</h2>
      <p class="side-event__when">Sunday, July 27<br>07:00 AM To 10:00 AM<br>Location Tba</p>
    </section>
    <section class="side-event side-event--ride">
      <h2 class="side-event__tag">Optional<br>Group Ride</h2>
      <p class="side-event__when">Saturday, July 26<br>10:00 AM To Noon</p>
    </section>

    <h2 class="raffle">Tarvex 450 Custom Cafe′ Motorcycle Raffle</h2>
    <p class="prizes">Contests, trophies and cash prizes for pin-up girl, coolest cafe′ racer motorcycle,<br>coolest mod scooter, peoples choice motorcycle, and more!</p>

    <p class="lineup">Live music by the one and only legendary KLTV,<br>“Slim Jim” Varga and more TBA.</p>

    <footer class="credits">
      <p class="credits__label">BROUGHT TO YOU BY:</p>
      <div class="sponsor sponsor--throttlers">
        <span class="sponsor__mark" aria-hidden="true"></span>
        <div>
          <p class="sponsor__name">Wyland Throttlers</p>
          <p class="sponsor__url">www.social.example/wylandthrottlers</p>
        </div>
      </div>
      <div class="sponsor sponsor--rascals">
        <span class="sponsor__mark" aria-hidden="true"></span>
        <div>
          <p class="sponsor__name">Bixby and Moss/<br>Moss Rascals</p>
          <p class="sponsor__url">www.bixbyandmoss.example</p>
        </div>
      </div>
      <p class="credits__beneficiaries">Partial Proceeds to benefit the UFWL and<br>The Valley Rescue Volunteers Society.<br>More information and advance tickets available at<br>www.gearheadrally.example</p>
    </footer>
  </main>
</body>
</html>
```